UI/ UX Design for ERP Software

We need a new UX/UI interface for a ERP software for property managers. Our CMMS / ERP solution is made based on responsive design technologies and is coded in PHP.
The overall UX to be similar to Tev Ulna - easy navigation, intuitive menus.

Industry/Entity Type

Property Management

Number of Pages Required

5+ page

Requirements
Must have
• Round dock buttons
Consistent icons across the application
Enough Spacing between buttons/icons/ menu
Consistent Font
Nice to have
• We would like the UX to allow the users to use the application without /minimum training.
Should not have
• we don't want anything that is classic with respect to UX

```html
<!DOCTYPE html>
<html lang="en">
<head>
<meta charset="utf-8">
<title>Estatly – Active Dashboard</title>
<link href="https://fonts.googleapis.com/css2?family=Poppins:wght@400;500;600&family=Open+Sans:wght@400;600;700&display=swap" rel="stylesheet">
<style>
:root{
  --page:#454545;
  --header-a:#0a7cfb;
  --header-b:#06b2f6;
  --tile:#f3f3f3;
  --tile-active:#222222;
  --icon:#7a7a7a;
  --panel:#ffffff;
  --content:#f3f3f3;
  --tabs:#0a9df1;
  --tab-active:#2b2b2b;
  --text:#262626;
  --card-properties:#6aab9a;
  --card-tenants:#f99584;
  --card-total:#e46b7b;
  --card-rented:#5b76dc;
  --card-vacant:#374a7c;
  --ring:#bdbdbd;
  --arc-top:#bcdaf6;
  --arc-bottom:#76b1ea;
  --pill:#7ab4ea;
}
*{box-sizing:border-box;margin:0;padding:0}
html,body{width:1200px;height:1029px;overflow:hidden;background:var(--page);font-family:'Poppins',sans-serif}
.canvas{position:relative;width:1200px;height:1029px}

.header{position:absolute;left:29px;top:34px;width:1142px;height:216px;border-radius:4px;
  background:linear-gradient(90deg,var(--header-a),var(--header-b))}
.brand{position:absolute;left:10px;top:22px;display:flex;align-items:center;gap:8px;color:#fff;
  font-weight:600;font-size:24px;letter-spacing:.2px}
.brand-mark{width:22px;height:22px;background:#fff;border-radius:50%}
.welcome{position:absolute;right:54px;top:26px;color:#fff;font-size:9.5px;font-weight:500}
.avatar{position:absolute;right:6px;top:14px;width:40px;height:40px;border-radius:50%;
  background:radial-gradient(circle at 50% 40%,#c9a78f,#6f5a4e);border:2px solid #e6eef7}

.dock{position:absolute;left:6px;top:67px;display:grid;grid-template-columns:repeat(12,91px);
  column-gap:3.6px;row-gap:4px}
.tile{height:68px;background:var(--tile);display:flex;align-items:center;justify-content:center}
.tile svg{width:26px;height:26px;fill:var(--icon)}
.tile.active{background:var(--tile-active)}
.tile.active svg{fill:#fff}
.tile.faint svg{fill:#b3b3b3}

.stats{position:absolute;left:29px;top:256px;width:1142px;height:75px;background:var(--panel);border-radius:4px}
.card{position:absolute;top:9px;width:222px;height:57px;color:#fff;font-family:'Open Sans',sans-serif}
.card svg{position:absolute;left:17px;top:14px;width:32px;height:30px;fill:#fff}
.card .label{position:absolute;left:72px;top:11px;font-size:11px;font-weight:600;text-transform:uppercase;letter-spacing:.2px}
.card .value{position:absolute;left:72px;top:25px;font-size:17px;font-weight:700}
.c1{left:6px;background:var(--card-properties)}
.c2{left:233px;background:var(--card-tenants)}
.c3{left:460px;background:var(--card-total)}
.c4{left:687px;background:var(--card-rented)}
.c5{left:914px;background:var(--card-vacant)}

.main{position:absolute;left:29px;top:338px;width:1142px;height:625px;background:var(--panel);border-radius:4px}
.title{position:absolute;left:6px;top:10px;display:flex;align-items:center;gap:9px;color:var(--text);
  font-size:36px;line-height:40px;font-weight:500}
.title svg{width:32px;height:28px;fill:var(--text)}
.tabs{position:absolute;left:6px;top:59px;width:1130px;height:37px;background:var(--tabs);
  border-bottom:3px solid #333;font-family:'Open Sans',sans-serif}
.tab{position:absolute;top:0;height:34px;display:flex;align-items:center;color:#fff;font-size:12.5px;gap:4px}
.tab svg{width:9px;height:9px}
.tab.sep{border-right:1px solid rgba(0,0,0,.12)}
.tab.active{background:var(--tab-active);top:5px;height:29px;padding-left:11px;width:94px;left:5px}
.content{position:absolute;left:6px;top:96px;width:1130px;height:524px;background:var(--content)}
.range{position:absolute;left:17px;top:16px;display:flex;align-items:center;gap:10px;font-size:17px;color:var(--text)}
.range svg{width:20px;height:16px;fill:var(--text)}
.chart{position:absolute;left:0;top:0;width:560px;height:524px}
.pill{position:absolute;left:220px;top:265px;width:122px;height:38px;border-radius:19px;background:var(--pill);
  color:#fff;font-size:17px;display:flex;align-items:center;justify-content:center}
.legend{position:absolute;left:716px;top:128px;width:268px;height:260px;background:#fff;list-style:none;padding-top:17px}
.legend li{display:flex;align-items:center;height:34.3px;padding-left:17px;font-size:11.5px}
.legend i{width:18px;height:18px;border-radius:50%;margin-right:12px;flex:none}
.footer{position:absolute;left:0;top:990px;width:1200px;text-align:center;color:#eee;font-family:'Open Sans',sans-serif;font-size:11.5px;word-spacing:3px}
</style>
</head>
<body>
<div class="canvas">
  <header class="header">
    <div class="brand"><span class="brand-mark"></span>Estatly</div>
    <div class="welcome">Welcome, Dana Reyes</div>
    <div class="avatar" role="img" aria-label="User profile photo"></div>
    <nav class="dock">
      <div class="tile active"><svg viewBox="0 0 24 24"><path d="M12 4a10 10 0 0 0-10 10c0 2 .6 3.8 1.6 5.3h16.8A10 10 0 0 0 12 4zm0 2.2a1.2 1.2 0 1 1 0 2.4 1.2 1.2 0 0 1 0-2.4zM6 9a1.2 1.2 0 1 1 0 2.4A1.2 1.2 0 0 1 6 9zm12 0a1.2 1.2 0 1 1 0 2.4A1.2 1.2 0 0 1 18 9zM4.8 14a1.2 1.2 0 1 1 0 .1zm14.4 0a1.2 1.2 0 1 1 0 .1zM13.5 8.5l.8.3-1.1 7a1.8 1.8 0 1 1-2.4-.6z"/></svg></div>
      <div class="tile"><svg viewBox="0 0 24 24"><circle cx="7" cy="7" r="3"/><circle cx="17" cy="7" r="3"/><circle cx="12" cy="10" r="3.3"/><path d="M1 17c0-3 2-5 5-5h2a6 6 0 0 0-2 6H1zM23 17c0-3-2-5-5-5h-2a6 6 0 0 1 2 6h5zM6 21c0-4 2.5-6.5 6-6.5s6 2.5 6 6.5z"/></svg></div>
      <div class="tile"><svg viewBox="0 0 24 24"><path d="M12 3 1 12.5l1.5 1.6L12 6l9.5 8.1 1.5-1.6zM17 4h3v5l-3-2.6zM5 14l7-6 7 6v7h-5v-5h-4v5H5z"/></svg></div>
      <div class="tile"><svg viewBox="0 0 24 24"><circle cx="12" cy="7.5" r="4.5"/><path d="M3 21c0-5 3.5-8 9-8s9 3 9 8z"/></svg></div>
      <div class="tile"><svg viewBox="0 0 24 24"><path d="M5 2h14a1 1 0 0 1 1 1v18a1 1 0 0 1-1 1H5a1 1 0 0 1-1-1v-2H3v-2h1v-3H3v-2h1V9H3V7h1V3a1 1 0 0 1 1-1zm2 2v16h11V4zm5.5 2.5a2.5 2.5 0 1 1 0 5 2.5 2.5 0 0 1 0-5zM8 17c0-2.5 2-4 4.5-4s4.5 1.5 4.5 4z"/></svg></div>
      <div class="tile"><svg viewBox="0 0 24 24"><path d="M8 6l1.6.4.9-1.4 1.5.9-.4 1.6 1.2 1.2 1.6-.4.9 1.5-1.4.9.4 1.6-.4 1.6 1.4.9-.9 1.5-1.6-.4-1.2 1.2.4 1.6-1.5.9-.9-1.4L8 18l-1.6-.4-.9 1.4-1.5-.9.4-1.6-1.2-1.2-1.6.4-.9-1.5 1.4-.9L2 12l.4-1.6L1 9.5l.9-1.5 1.6.4 1.2-1.2-.4-1.6L5.8 4.7l.9 1.4zm0 3.3a2.7 2.7 0 1 0 0 5.4 2.7 2.7 0 0 0 0-5.4z"/><circle cx="18.5" cy="5.5" r="3.5"/><circle cx="18.5" cy="17.5" r="3.5"/></svg></div>
      <div class="tile"><svg viewBox="0 0 24 24"><circle cx="5" cy="8" r="2.6"/><circle cx="19" cy="8" r="2.6"/><circle cx="12" cy="7" r="3.4"/><path d="M0 18c0-3 2-5 5-5 1 0 2 .3 2.6.8A6 6 0 0 0 6 18zM24 18c0-3-2-5-5-5-1 0-2 .3-2.6.8A6 6 0 0 1 18 18zM7 19c0-4 2.2-6.5 5-6.5s5 2.5 5 6.5z"/></svg></div>
      <div class="tile"><svg viewBox="0 0 24 24"><path d="M5 2h9l5 5v15H5zm8 1v5h5zM8 18c1-1 3-5 4-9 .5 2 2 4 4 5-2 0-6 1-8 4z"/></svg></div>
      <div class="tile"><svg viewBox="0 0 24 24"><path d="M12 2a10 10 0 1 1 0 20 10 10 0 0 1 0-20zm0 6a4 4 0 1 0 0 8 4 4 0 0 0 0-8zM5.5 7 8 9.5l1.5-1.5L7 5.5zm13 0L16 9.5 14.5 8 17 5.5zm-13 10L8 14.5l1.5 1.5L7 18.5zm13 0L16 14.5 14.5 16 17 18.5z"/></svg></div>
      <div class="tile"><svg viewBox="0 0 24 24"><path d="M9 2h6v5h-2v2h7v4h2v6h-6v-6h2v-2h-5v2h2v6H9v-6h2v-2H6v2h2v6H2v-6h2v-4h7V7H9z"/></svg></div>
      <div class="tile"><svg viewBox="0 0 24 24"><path d="M7 6l1.4 1.4L3.8 12l4.6 4.6L7 18l-6-6zm10 0 6 6-6 6-1.4-1.4 4.6-4.6-4.6-4.6zM13.5 4l1.9.6-4.9 15.4-1.9-.6z"/></svg></div>
      <div class="tile"><svg viewBox="0 0 24 24"><path d="M10 2a8 8 0 0 1 6.3 12.9l6 6-1.5 1.5-6-6A8 8 0 1 1 10 2zm0 2.5a5.5 5.5 0 1 0 0 11 5.5 5.5 0 0 0 0-11z"/></svg></div>

      <div class="tile"><svg viewBox="0 0 24 24"><path d="M2 3h2v16h18v2H2zm4 8h2v6H6zm4-4h2v10h-2zm4 2h2v8h-2zm4-5h2v13h-2z"/></svg></div>
      <div class="tile"><svg viewBox="0 0 24 24"><path d="M12 2 23 21H1zm-1.3 6v6.5h2.6V8zm0 8v2.6h2.6V16z"/></svg></div>
      <div class="tile"><svg viewBox="0 0 24 24"><path d="M9 2h6v5h-2v2h7v4h2v6h-6v-6h2v-2h-5v2h2v6H9v-6h2v-2H6v2h2v6H2v-6h2v-4h7V7H9z"/></svg></div>
      <div class="tile"><svg viewBox="0 0 24 24"><path d="M1 5h22v14H1zm2 2v10h18V7zm9 1.5a3.5 3.5 0 1 1 0 7 3.5 3.5 0 0 1 0-7zM11 10v1h.8v3h1.2v-4z"/></svg></div>
      <div class="tile"><svg viewBox="0 0 24 24"><path d="M9 3c4.4 0 8 2.6 8 6s-3.6 6-8 6c-.8 0-1.6-.1-2.300-.3L3 17l1-3.2C2.200 12.700 1 11 1 9c0-3.4 3.600-6 8-6zm9.500 5.500c2.800.9 4.500 2.900 4.500 5 0 1.600-.8 3-2.200 3.900l.9 2.600-3.200-1.600c-.6.1-1.200.2-1.900.2-2.500 0-4.700-1-5.800-2.600 4.500-.3 7.900-3.300 7.700-7.500z"/></svg></div>
      <div class="tile"><svg viewBox="0 0 24 24"><path d="M5 2h9v6h6v14H5zm10 0 5 5h-5z"/></svg></div>
      <div class="tile"><svg viewBox="0 0 24 24"><path d="M2 3h2v16h18v2H2zm3 14V12l4-5 4 4 3-3 5 4v5z"/></svg></div>
      <div class="tile"><svg viewBox="0 0 24 24"><path d="M5 2h9v6h6v14H5zm10 0 5 5h-5zM8 11v1.6h9V11zm0 3.5v1.6h9v-1.6zm0 3.5v1.6h9V18z"/></svg></div>
      <div class="tile"><svg viewBox="0 0 24 24"><path d="M2 4h20v16H2zm2 3v11h7V7zm9 0v11h7V7z"/></svg></div>
      <div class="tile"><svg viewBox="0 0 24 24"><path d="M10.3 1h3.4l.6 3 2 .9 2.6-1.7 2.4 2.4-1.7 2.6.9 2 3 .6v3.4l-3 .6-.9 2 1.7 2.6-2.4 2.4-2.6-1.7-2 .9-.6 3h-3.4l-.6-3-2-.9-2.6 1.7-2.4-2.4 1.7-2.6-.9-2-3-.6v-3.4l3-.6.9-2-1.7-2.6 2.4-2.4 2.6 1.7 2-.9zM12 8a4 4 0 1 0 0 8 4 4 0 0 0 0-8z"/></svg></div>
      <div class="tile"><svg viewBox="0 0 24 24"><path d="M21 6.5 17.5 10 14 9l-1-3.5L16.5 2A6 6 0 0 0 9 9.5L2 16.5a2.5 2.5 0 0 0 3.5 3.5l7-7A6 6 0 0 0 21 6.5z"/></svg></div>
      <div class="tile faint"><svg viewBox="0 0 24 24"><path d="M12 2 22 12l-2 2-6.5-6.3V22h-3V7.7L4 14l-2-2z"/></svg></div>
    </nav>
  </header>

  <section class="stats">
    <div class="card c1"><svg viewBox="0 0 24 24"><path d="M12 3 1 12.5l1.5 1.6L12 6l9.5 8.1 1.5-1.6zM17 4h3v5l-3-2.6zM5 14l7-6 7 6v7h-5v-5h-4v5H5z"/></svg><div class="label">Properties</div><div class="value">3</div></div>
    <div class="card c2"><svg viewBox="0 0 24 24"><circle cx="5" cy="8" r="2.6"/><circle cx="19" cy="8" r="2.6"/><circle cx="12" cy="7" r="3.4"/><path d="M0 18c0-3 2-5 5-5 1 0 2 .3 2.6.8A6 6 0 0 0 6 18zM24 18c0-3-2-5-5-5-1 0-2 .3-2.6.8A6 6 0 0 1 18 18zM7 19c0-4 2.2-6.5 5-6.5s5 2.5 5 6.5z"/></svg><div class="label">Tenants</div><div class="value">8</div></div>
    <div class="card c3"><svg viewBox="0 0 24 24"><path d="M12 1l4 4h-2.5v5.5H19V8l4 4-4 4v-2.5h-5.5V19H16l-4 4-4-4h2.5v-5.5H5V16l-4-4 4-4v2.5h5.5V5H8z"/></svg><div class="label">Total Properties Area</div><div class="value">422,000.00 sq.ft.</div></div>
    <div class="card c4"><svg viewBox="0 0 24 24"><path d="M12 1l4 4h-2.5v5.5H19V8l4 4-4 4v-2.5h-5.5V19H16l-4 4-4-4h2.5v-5.5H5V16l-4-4 4-4v2.5h5.5V5H8z"/></svg><div class="label">Rented Area</div><div class="value">233,500.00 sq.ft.</div></div>
    <div class="card c5"><svg viewBox="0 0 24 24"><path d="M12 1l4 4h-2.5v5.5H19V8l4 4-4 4v-2.5h-5.5V19H16l-4 4-4-4h2.5v-5.5H5V16l-4-4 4-4v2.5h5.5V5H8z"/></svg><div class="label">Vacancies Area</div><div class="value">188,500.00 sq.ft.</div></div>
  </section>

  <main class="main">
    <h1 class="title"><svg viewBox="0 0 24 21"><path d="M12 1 1 10.5l1.5 1.6L12 4l9.5 8.1 1.5-1.6zM17 2h3v5l-3-2.6zM5 12l7-6 7 6v8h-5v-5h-4v5H5z"/></svg>Active Dashboard</h1>
    <div class="tabs">
      <div class="tab active"><svg viewBox="0 0 10 10"><circle cx="5" cy="5" r="4" fill="none" stroke="#fff" stroke-width="1.4"/><path d="M5 2.5V5h2" fill="none" stroke="#fff" stroke-width="1.2"/></svg>Last 7 days</div>
      <div class="tab sep" style="left:99px;width:103px;padding-left:11px"><svg viewBox="0 0 10 10"><circle cx="5" cy="5" r="4" fill="none" stroke="#fff" stroke-width="1.4"/><path d="M5 2.5V5h2" fill="none" stroke="#fff" stroke-width="1.2"/></svg>Last months</div>
      <div class="tab sep" style="left:202px;width:116px;padding-left:14px"><svg viewBox="0 0 10 10"><circle cx="5" cy="5" r="4" fill="none" stroke="#fff" stroke-width="1.4"/><path d="M5 2.5V5h2" fill="none" stroke="#fff" stroke-width="1.2"/></svg>Last 3 months</div>
      <div class="tab sep" style="left:318px;width:103px;padding-left:14px"><svg viewBox="0 0 10 10"><circle cx="5" cy="5" r="4" fill="none" stroke="#fff" stroke-width="1.4"/><path d="M5 2.5V5h2" fill="none" stroke="#fff" stroke-width="1.2"/></svg>Next 7 days</div>
      <div class="tab sep" style="left:421px;width:109px;padding-left:13px"><svg viewBox="0 0 10 10"><circle cx="5" cy="5" r="4" fill="none" stroke="#fff" stroke-width="1.4"/><path d="M5 2.5V5h2" fill="none" stroke="#fff" stroke-width="1.2"/></svg>Next months</div>
      <div class="tab sep" style="left:530px;width:122px;padding-left:14px"><svg viewBox="0 0 10 10"><circle cx="5" cy="5" r="4" fill="none" stroke="#fff" stroke-width="1.4"/><path d="M5 2.5V5h2" fill="none" stroke="#fff" stroke-width="1.2"/></svg>Next 3 months</div>
    </div>
    <div class="content">
      <div class="range"><svg viewBox="0 0 24 20"><path d="M1 1h2v16h20v2H1zm4 8h2.5v6H5zm4.5-4H12v10H9.5zm4.5 3h2.5v7H14zm4.5-5H21v12h-2.5z"/></svg>12/27/2020 - 01/03/2021</div>
      <svg class="chart" viewBox="0 0 560 524" role="img" aria-label="Schedule ring for the selected week">
        <defs>
          <linearGradient id="arcFill" x1="0" y1="0" x2="0" y2="1">
            <stop offset="0" stop-color="#bcdaf6"/>
            <stop offset="1" stop-color="#76b1ea"/>
          </linearGradient>
        </defs>
        <circle cx="281" cy="284" r="211" fill="none" stroke="#bdbdbd" stroke-width="1.5"/>
        <path d="M281 73 A211 211 0 0 1 281 495" fill="none" stroke="url(#arcFill)" stroke-width="22"/>
      </svg>
      <div class="pill">12/30/2020</div>
      <ul class="legend">
        <li style="color:#7ab0e8"><i style="background:#7ab4ea"></i>Scheduled Maintenance</li>
        <li style="color:#5cc45a"><i style="background:#8ee27a"></i>Completed Scheduled Maintenance</li>
        <li style="color:#f4a050"><i style="background:#f7a458"></i>Future Scheduled Maintenance</li>
        <li style="color:#333"><i style="background:#3f4045"></i>Scheduled Work Orders</li>
        <li style="color:#7c80e6"><i style="background:#8486ee"></i>Completed Work Orders</li>
        <li style="color:#e9557a"><i style="background:#ee5b7e"></i>Property Inspections in Progress</li>
        <li style="color:#c9b22a"><i style="background:#e6d05a"></i>Completed Property Inspections</li>
      </ul>
    </div>
  </main>

  <footer class="footer">Copyright © 2021 Estatly. All rights reserved.</footer>
</div>
</body>
</html>
```